Business Card Design Project

After recently finishing a design project for the company logo using markbazaar, it's now time for a business card. Attached to this is the logo.

The requirements for the business card are pretty straightforward:

- A clean, uncomplicated look
- Consistent usage of fonts
- Designs for both single sided and double sided cards
- A modern layout with preferably space to refer to social media accounts and/or downloadable vcards through a qr code
- consistent application of the company colour scheme: red/white. Hex codes for exact colour can be provided

Thanks!

```html
<!DOCTYPE html>
<html lang="en">
<head>
<meta charset="utf-8">
<title>Kilnstone Recruiting – Business Cards</title>
<link rel="stylesheet" href="https://fonts.googleapis.com/css2?family=Open+Sans:wght@400;500;700&display=swap">
<style>
  :root {
    --brand-red: #e31e24;
    --ink: #231f20;
    --ink-soft: #333333;
    --card: #ffffff;
    --backdrop: #e9e6e2;
  }
  * { margin: 0; padding: 0; box-sizing: border-box; }
  html, body { width: 960px; height: 1200px; overflow: hidden; }
  body {
    position: relative;
    background: var(--backdrop);
    font-family: "Open Sans", Arial, sans-serif;
    color: var(--ink);
  }
  .card {
    position: absolute;
    left: 55px;
    width: 840px;
    height: 480px;
    background: var(--card);
    border-radius: 28px;
    box-shadow: 0 4px 10px rgba(0,0,0,0.18);
    overflow: hidden;
  }
  .card--front { top: 72px; }
  .card--back { top: 638px; }

  .wordmark {
    position: absolute;
    display: flex;
    align-items: center;
    gap: 26px;
  }
  .wordmark__square {
    background: var(--brand-red);
    flex: none;
  }
  .wordmark__name {
    font-weight: 500;
    color: var(--ink);
    line-height: 1;
  }
  .wordmark__line { display: block; }
  .wordmark__line--sub { letter-spacing: 0.34em; }

  .card--front .wordmark { left: 50px; top: 78px; }
  .card--front .wordmark__square { width: 74px; height: 74px; }
  .card--front .wordmark__line--main { font-size: 78px; letter-spacing: -0.01em; }
  .card--front .wordmark__line--sub { font-size: 40px; margin-top: 14px; }

  .accent-bar {
    position: absolute;
    left: 0; top: 288px;
    width: 10px; height: 58px;
    background: var(--brand-red);
  }
  .person { position: absolute; left: 49px; top: 288px; }
  .person__name { font-size: 24px; font-weight: 700; color: var(--brand-red); line-height: 1.2; }
  .person__role { font-size: 19px; color: var(--ink-soft); margin-top: 2px; }

  .contact { position: absolute; left: 49px; top: 364px; list-style: none; }
  .contact__item {
    display: flex; align-items: center; gap: 8px;
    font-size: 21px; color: var(--ink-soft); height: 34px;
  }
  .contact__icon { width: 14px; height: 14px; fill: var(--ink-soft); flex: none; }

  .address {
    position: absolute; left: 479px; top: 370px;
    font-style: normal; font-size: 21px; line-height: 32px; color: var(--ink-soft);
  }

  .card--back .wordmark { left: 50px; top: 58px; }
  .card--back .wordmark__line--main { font-size: 84px; letter-spacing: -0.01em; }
  .card--back .wordmark__line--sub { font-size: 44px; margin-top: 16px; }
  .back-square {
    position: absolute; left: 560px; top: 190px;
    width: 220px; height: 220px;
    background: var(--brand-red);
  }
</style>
</head>
<body>

<section class="card card--front" aria-label="Card front">
  <div class="wordmark">
    <span class="wordmark__square"></span>
    <span class="wordmark__name">
      <span class="wordmark__line wordmark__line--main">Kilnstone</span>
      <span class="wordmark__line wordmark__line--sub">RECRUITING</span>
    </span>
  </div>

  <span class="accent-bar"></span>
  <div class="person">
    <p class="person__name">Your Name</p>
    <p class="person__role">Designation</p>
  </div>

  <ul class="contact">
    <li class="contact__item">
      <svg class="contact__icon" viewBox="0 0 14 14" aria-hidden="true"><path d="M1 5c0-2 2.5-3 6-3s6 1 6 3v1h-3V5H4v1H1zM3 7h8l1 5H2z"/></svg>
      123-123-1234
    </li>
    <li class="contact__item">
      <svg class="contact__icon" viewBox="0 0 14 14" aria-hidden="true"><path d="M1 3h12v8H1zM2 4v.5l5 3.5 5-3.5V4zm0 2v4h10V6L7 9.3z" fill-rule="evenodd"/></svg>
      info@yourwebsite.com
    </li>
    <li class="contact__item">
      <svg class="contact__icon" viewBox="0 0 14 14" aria-hidden="true"><circle cx="7" cy="7" r="5.5"/></svg>
      www.kilnstone.com
    </li>
  </ul>

  <address class="address">
    1234, Street Name<br>
    District, City<br>
    Country Code.
  </address>
</section>

<section class="card card--back" aria-label="Card back">
  <div class="wordmark">
    <span class="wordmark__name">
      <span class="wordmark__line wordmark__line--main">Kilnstone</span>
      <span class="wordmark__line wordmark__line--sub">RECRUITING</span>
    </span>
  </div>
  <span class="back-square"></span>
</section>

</body>
</html>
```